We need a Word Template for Custom Laboratory Results from an independent laboratory

The test is a novel biomarker for a chronic pain condition called endometriosis. It is expressed as a percentage. We will upload a sample result. We are looking for improved graphic fidelity with more attention to design and spacing. Emphasis should be placed on the overall result, i.e. the patient percentage results. Considerationis going to be given to the most appealing graphic result.

Target Market(s)

Women aged 19-45

Colors
0054AA
0677BA
7BADD7
CADEEF
E8F1F8

```html
<!DOCTYPE html>
<html lang="en">
<head>
<meta charset="utf-8">
<title>Endometriosis Assay Result Report</title>
<link rel="stylesheet" href="https://fonts.googleapis.com/css2?family=Carlito:wght@400;700&family=Arimo:wght@700&display=swap">
<style>
  :root {
    --backdrop: #d9d9d9;
    --paper: #eeeeee;
    --rule: #555555;
    --label-fill: #c6c6c6;
    --ink: #1e1e1e;
    --clinic-grey: #4f5558;
    --partner-blue: #2e3f9c;
    --title-blue: #4a8fd6;
    --band-blue: #4f8fd1;
    --result-fill: #c2dbec;
    --result-red: #cc1111;
  }
  * { box-sizing: border-box; margin: 0; padding: 0; }
  html, body { width: 1200px; height: 1200px; overflow: hidden; }
  body {
    background: var(--backdrop);
    font-family: "Carlito", "Calibri", sans-serif;
    color: var(--ink);
    position: relative;
  }
  .report {
    position: absolute; left: 200px; top: 40px;
    width: 800px; height: 1120px;
    background: var(--paper);
  }
  .clinic-brand {
    position: absolute; left: 47px; top: 40px;
    display: flex; align-items: center; gap: 12px;
    color: var(--clinic-grey);
  }
  .clinic-mark {
    width: 54px; height: 54px; border-radius: 50%;
    background: #7fa6b2;
  }
  .clinic-name { font-size: 24px; font-weight: 400; line-height: 1.1; }
  .partner-brand {
    position: absolute; right: 44px; top: 48px;
    font-size: 36px; font-weight: 700; color: var(--partner-blue);
  }
  .report-title {
    position: absolute; left: 0; right: 0; top: 208px;
    text-align: center; font-size: 27px; font-weight: 700;
    letter-spacing: 1px; color: var(--title-blue);
  }
  .patient-table {
    position: absolute; left: 47px; top: 270px; width: 708px;
    border-collapse: collapse;
  }
  .patient-table th, .patient-table td {
    border: 1px solid var(--rule); height: 49px;
  }
  .patient-table th {
    width: 170px; background: var(--label-fill);
    text-align: left; padding-left: 8px;
    font-size: 19px; font-weight: 700;
  }
  .results-band {
    position: absolute; left: 47px; top: 452px; width: 708px; height: 41px;
    background: var(--band-blue); color: #fff;
    font-size: 22px; font-weight: 700; letter-spacing: 0.5px;
    display: flex; align-items: center; justify-content: center;
    box-shadow: 0 2px 3px rgba(0,0,0,0.25);
  }
  .result-box {
    position: absolute; left: 47px; top: 560px; width: 709px; height: 201px;
    border: 1px solid var(--rule); display: flex;
  }
  .result-label {
    width: 415px; border-right: 1px solid var(--rule);
    display: flex; flex-direction: column; align-items: center; justify-content: center;
    font-size: 19.5px; line-height: 1.38; text-align: center;
  }
  .result-label strong { font-weight: 700; }
  .result-value {
    flex: 1; background: var(--result-fill);
    display: flex; align-items: center; justify-content: center;
    font-family: "Arimo", "Arial", sans-serif; font-weight: 700;
    font-size: 62px; color: var(--result-red);
  }
  .reference-box {
    position: absolute; left: 47px; top: 916px; width: 385px; height: 147px;
    border: 1px solid var(--rule); padding: 18px 0 0 32px;
    font-size: 14px; line-height: 18px;
  }
  .reference-heading { font-weight: 700; text-decoration: underline; }
  .reference-list { list-style: none; }
  .reference-list li { display: flex; }
  .reference-list .num { width: 24px; }
</style>
</head>
<body>
  <main class="report">
    <div class="clinic-brand">
      <span class="clinic-mark"></span>
      <span class="clinic-name">Meridian<br>Fertility London</span>
    </div>
    <div class="partner-brand">Lumeva</div>

    <h1 class="report-title">ENDOSIGN MICRO-RNA ENDOMETRIOSIS ASSAY</h1>

    <table class="patient-table">
      <tr><th>NAME</th><td></td></tr>
      <tr><th>OHIP NUMBER</th><td></td></tr>
      <tr><th>DATE OF BIRTH</th><td></td></tr>
    </table>

    <div class="results-band">YOUR RESULTS</div>

    <section class="result-box">
      <div class="result-label">
        <span>Predicted Probability of Endometriosis</span>
        <span>Compared to Surgical Controls</span>
        <strong>(100% probability)</strong>
      </div>
      <div class="result-value">38.7%</div>
    </section>

    <section class="reference-box">
      <div class="reference-heading">Reference Range</div>
      <ol class="reference-list">
        <li><span class="num">1.</span>0.0-29.9% - &nbsp;low probability of endometriosis</li>
        <li><span class="num">2.</span>29.9-44.9% - inconclusive</li>
        <li><span class="num">3.</span>45.0-55.0% - intermediate risk of endometriosis</li>
        <li><span class="num">4.</span>55.1-64.9% - probable endometriosis</li>
        <li><span class="num">5.</span>65.0-99.9% - highly probable endometriosis</li>
      </ol>
    </section>
  </main>
</body>
</html>
```